Book Cover "Hushed"

Book summary:

Mara Pollins emerged from the oily wash of the Seine five years ago with no memory of her life, but an uncanny knowledge of fine art, museum security, and a knack for walking away with priceless treasures. Now she's tracking an elusive Ter Haalst with ties to an underworld struggle that will reveal her forgotten past. 

She leaves Paris to track a priceless painting from St. Pete to Chicago. Her contacts are shady and she is beginning to think there is more to this job than a buyer wanting a gift for his wife. Otherwise, why would Gareth Linsey, a rival thief, cross her path just as the KTR begins asking questions?

Caught up in the six billion dollar international art theft industry, she enlists help from unlikely sources: film actor Neil Barto, and veteran KTR specialists Dougal Pryce and Peter Hale.

>> This novel is currently on Pagerill.com with free sample downloads available.

>> This is the first book in a series - future titles will also feature art crime suspense theme, with international locations.

>> eBook file available upon request via email.

```html
<!DOCTYPE html>
<html lang="en">
<head>
<meta charset="utf-8">
<title>Hushed — Mara Pollins</title>
<link rel="stylesheet" href="https://fonts.googleapis.com/css2?family=Titan+One&family=EB+Garamond:ital,wght@1,400&display=swap">
<style>
  :root {
    --paper-light: #ddd0bc;
    --paper-mid: #cbb9a0;
    --paper-dark: #a8937a;
    --cord: #e6dccb;
    --cord-shade: #9e8c74;
    --gold-light: #f3d66a;
    --gold: #d4a83a;
    --gold-deep: #8f6a1c;
    --skyline-ink: #1a1612;
    --skyline-paper: #efe4cc;
    --band-edge: #e9dcc0;
    --band-yellow: #f6ec4a;
    --band-yellow-light: #fbf59a;
    --ink: #0d0c0a;
  }
  * { margin: 0; padding: 0; box-sizing: border-box; }
  html, body { width: 900px; height: 1200px; overflow: hidden; }
  body { background: var(--paper-mid); }

  .cover {
    position: relative;
    width: 900px;
    height: 1200px;
    overflow: hidden;
    background: radial-gradient(ellipse at 50% 40%, var(--paper-light) 0%, var(--paper-mid) 55%, var(--paper-dark) 100%);
  }

  .hanging-cord { position: absolute; inset: 0; width: 900px; height: 1200px; }

  .picture-frame {
    position: absolute;
    left: 85px;
    top: 265px;
    width: 740px;
    height: 450px;
    transform: rotate(-14deg);
    border: 56px solid var(--gold);
    border-image: linear-gradient(135deg, var(--gold-light), var(--gold) 35%, var(--gold-deep) 60%, var(--gold) 80%, var(--gold-light)) 1;
    background: transparent;
    box-shadow: 6px 10px 18px rgba(60, 40, 20, 0.35);
  }
  .picture-frame::before {
    content: "";
    position: absolute;
    inset: -14px;
    border: 6px solid var(--gold-light);
    pointer-events: none;
  }
  .skyline {
    position: absolute;
    left: 0;
    right: 0;
    bottom: 0;
    height: 150px;
    background: linear-gradient(to bottom, var(--skyline-paper) 0%, var(--skyline-paper) 28%, var(--skyline-ink) 28%, var(--skyline-ink) 100%);
  }

  .title-band {
    position: absolute;
    left: 0;
    top: 786px;
    width: 900px;
    height: 254px;
    background: var(--band-edge);
    padding: 20px 0;
  }
  .title-band__strip {
    height: 100%;
    background: linear-gradient(to bottom, var(--band-yellow-light), var(--band-yellow) 40%, var(--band-yellow));
    display: flex;
    align-items: center;
    justify-content: center;
  }
  .title {
    font-family: "Titan One", "Cooper Black", sans-serif;
    font-size: 205px;
    line-height: 1;
    letter-spacing: 4px;
    color: var(--ink);
    text-transform: uppercase;
    transform: scaleY(0.95);
  }

  .author {
    position: absolute;
    right: 50px;
    top: 1068px;
    font-family: "EB Garamond", Garamond, serif;
    font-style: italic;
    font-size: 86px;
    line-height: 1;
    color: var(--ink);
  }
</style>
</head>
<body>
  <main class="cover">
    <svg class="hanging-cord" viewBox="0 0 900 1200" aria-hidden="true">
      <g stroke-linecap="round" fill="none">
        <path d="M248 0 L152 258" stroke="var(--cord-shade)" stroke-width="7"/>
        <path d="M248 0 L152 258" stroke="var(--cord)" stroke-width="4"/>
        <path d="M500 0 L790 278" stroke="var(--cord-shade)" stroke-width="7"/>
        <path d="M500 0 L790 278" stroke="var(--cord)" stroke-width="4"/>
      </g>
    </svg>

    <div class="picture-frame">
      <div class="skyline" role="img" aria-label="Black silhouette of the Paris skyline with the Eiffel Tower on torn paper"></div>
    </div>

    <div class="title-band">
      <div class="title-band__strip">
        <h1 class="title">Hushed</h1>
      </div>
    </div>

    <p class="author">Mara Pollins</p>
  </main>
</body>
</html>
```